Business card design needed

This is a new business and a unique service.
The market is academic staff at universities in Australia.
The services include workshops, seminars, individual research planning, individual support to develop grant applications for major funding. I will travel to work with people or work electronically with individuals. I have a highly successful track record and am known in many universities for work done in the past.

Target Market(s)

university professorial staff and junior academic staff in australia

Industry/Entity Type

Travel

Contact Information for Business Card

The Scholar Summit
Charting Routes to Study Grants

Dr Helen T Brisk

www.scholarsummit.com.au
E: info@scholarsummit.com.au
Ph: 0438 602741

Requirements
Must have
• I want a classic simple design. Colours - clean shades of blue with a contrast (not browns or orange).
I want to see line used as the primary feature, diagonal or other acute angles through part of the card.
Fonts should be crisp, angular and highly readable. Use upper and lower case in all text (except email and web address)
A simple logo based on TSS would be good.
Card can be designed vertically if the design works best that way.

```html
<!DOCTYPE html>
<html lang="en">
<head>
<meta charset="utf-8">
<title>The Scholar Summit – Business Card</title>
<link rel="stylesheet" href="https://fonts.googleapis.com/css2?family=Open+Sans:wght@400;600&display=swap">
<style>
  :root {
    --page-bg: #e9ebee;
    --navy-deep: #03163f;
    --navy: #0a3a7e;
    --cyan-glow: #14a6d6;
    --silver-light: #f4f5f6;
    --silver-mid: #d2d4d7;
    --ink: #2a2a2a;
    --brand-blue: #0b4f93;
    --label-blue: #0b5fb0;
    --white: #ffffff;
  }
  html, body {
    margin: 0;
    width: 1200px;
    height: 900px;
    overflow: hidden;
    background: var(--page-bg);
    font-family: "Open Sans", "Segoe UI", sans-serif;
  }
  .sheet {
    position: relative;
    width: 1200px;
    height: 900px;
  }
  .card {
    position: absolute;
    left: 300px;
    width: 600px;
    height: 343px;
    overflow: hidden;
    box-shadow: 0 6px 18px rgba(0,0,0,0.18);
  }
  .card-front {
    top: 80px;
    background:
      radial-gradient(ellipse 45% 60% at 62% 60%, rgba(20,166,214,0.95), rgba(20,166,214,0) 70%),
      linear-gradient(125deg, var(--navy-deep) 0%, var(--navy) 45%, #1472b4 65%, var(--navy) 85%, var(--navy-deep) 100%);
  }
  .card-back {
    top: 477px;
    background: linear-gradient(125deg, var(--silver-light) 0%, var(--white) 40%, var(--silver-mid) 75%, #bfc2c6 100%);
  }
  .edge-lines {
    position: absolute;
    inset: 0;
    width: 100%;
    height: 100%;
  }
  .front-brand {
    position: absolute;
    left: 140px;
    top: 152px;
    margin: 0;
    color: var(--white);
    font-weight: 600;
    font-size: 22px;
    letter-spacing: 1px;
  }
  .back-brand {
    position: absolute;
    left: 46px;
    top: 72px;
    margin: 0;
    color: var(--brand-blue);
    font-weight: 600;
    font-size: 18px;
    letter-spacing: 0.5px;
  }
  .tagline {
    position: absolute;
    left: 46px;
    top: 100px;
    margin: 0;
    color: var(--ink);
    font-size: 13px;
  }
  .contact {
    position: absolute;
    right: 48px;
    top: 178px;
    margin: 0;
    text-align: right;
    color: var(--ink);
    font-style: normal;
    font-size: 18px;
    line-height: 27px;
  }
  .contact .person {
    display: block;
    font-size: 24px;
    line-height: 36px;
  }
  .contact .label {
    color: var(--label-blue);
    font-weight: 600;
  }
</style>
</head>
<body>
<main class="sheet">

  <section class="card card-front" aria-label="Card front">
    <svg class="edge-lines" viewBox="0 0 600 343" aria-hidden="true">
      <defs>
        <linearGradient id="front-sheen" x1="0" y1="0" x2="1" y2="0">
          <stop offset="0" stop-color="#ffffff" stop-opacity="0"/>
          <stop offset="0.55" stop-color="#ffffff" stop-opacity="0.95"/>
          <stop offset="1" stop-color="#ffffff" stop-opacity="0.6"/>
        </linearGradient>
      </defs>
      <polygon points="30,40 430,0 600,0 600,4" fill="url(#front-sheen)"/>
      <polygon points="30,40 600,4 600,8 40,44" fill="#ffffff" fill-opacity="0.25"/>
    </svg>
    <h1 class="front-brand">The Scholar Summit</h1>
  </section>

  <section class="card card-back" aria-label="Card back">
    <svg class="edge-lines" viewBox="0 0 600 343" aria-hidden="true">
      <defs>
        <linearGradient id="back-wedge" x1="0" y1="0" x2="1" y2="0">
          <stop offset="0" stop-color="#0a3a7e" stop-opacity="0"/>
          <stop offset="0.6" stop-color="#0a3a7e" stop-opacity="0.85"/>
          <stop offset="1" stop-color="#03163f"/>
        </linearGradient>
        <linearGradient id="back-wedge-light" x1="0" y1="0" x2="1" y2="0">
          <stop offset="0" stop-color="#5a86b8" stop-opacity="0"/>
          <stop offset="1" stop-color="#3d6fa8" stop-opacity="0.8"/>
        </linearGradient>
      </defs>
      <polygon points="30,36 600,0 600,10" fill="url(#back-wedge)"/>
      <polygon points="150,56 600,10 600,16" fill="url(#back-wedge-light)"/>
    </svg>
    <h2 class="back-brand">The Scholar Summit</h2>
    <p class="tagline">Charting Routes to Study Grants</p>
    <address class="contact">
      <span class="person">Dr Helen T Brisk</span>
      www.scholarsummit.com.au<br>
      <span class="label">E:</span> info@scholarsummit.com.au<br>
      <span class="label">P:</span> 0438 602741
    </address>
  </section>

</main>
</body>
</html>
```